Structural Engineering Business Card

Brookvane Drafting does residential house plans for clients in Central Florida. Would like simple but elegant business card that is appropriate for a house plan engineering company. Prefer black business card with black/white them but open to other shades of blue. I uploaded a sample card that I came across that looked good but please come up with your own creative designs.

Contact Information for Business Card

Name, Title, Phone, Email, Address, website

```html
<!DOCTYPE html>
<html lang="en">
<head>
<meta charset="utf-8">
<title>Brookvane Drafting Business Card</title>
<link href="https://fonts.googleapis.com/css2?family=Poppins:wght@400;700;800&display=swap" rel="stylesheet">
<style>
  :root {
    --backdrop: #2b2b2b;
    --card: #0a0a0a;
    --ink: #ffffff;
    --ink-soft: #e6e6e6;
    --rule: #5a5a5a;
  }
  * { box-sizing: border-box; margin: 0; padding: 0; }
  html, body {
    width: 1200px; height: 900px; overflow: hidden;
    background: var(--backdrop);
    font-family: "Poppins", sans-serif;
    color: var(--ink);
  }
  .sheet {
    width: 1200px; height: 900px;
    display: flex; align-items: center; justify-content: center; gap: 40px;
  }
  .card {
    width: 540px; height: 308px;
    background: var(--card);
    border-radius: 22px;
    position: relative;
    box-shadow: 0 10px 30px rgba(0,0,0,0.45);
  }
  /* Front: contact side */
  .card--front { display: flex; align-items: center; }
  .front-brand {
    width: 276px; padding-left: 36px; padding-top: 70px;
  }
  .brand-name {
    font-weight: 800; color: var(--ink);
    text-transform: uppercase; letter-spacing: 0.5px; line-height: 1.05;
  }
  .front-brand .brand-name { font-size: 26px; }
  .divider {
    width: 1px; height: 196px; background: var(--rule);
  }
  .contact { padding-left: 22px; }
  .person-name { font-size: 19px; font-weight: 700; letter-spacing: 0.6px; line-height: 1.1; }
  .person-title { font-size: 13px; color: var(--ink-soft); margin-bottom: 14px; }
  .contact-list { list-style: none; font-size: 13.5px; line-height: 1.55; }
  .contact-list li { display: flex; align-items: center; gap: 7px; }
  .contact-list svg { width: 13px; height: 13px; flex: none; }
  .address { font-size: 13.5px; line-height: 1.4; margin-top: 10px; padding-left: 20px; }
  /* Back: brand side */
  .card--back { display: flex; align-items: center; justify-content: center; }
  .card--back .brand-name { font-size: 44px; text-align: center; }
</style>
</head>
<body>
<main class="sheet">
  <section class="card card--front" aria-label="Business card front">
    <div class="front-brand">
      <p class="brand-name">Brookvane<br>Drafting</p>
    </div>
    <div class="divider"></div>
    <div class="contact">
      <p class="person-name">DANIEL HARPER</p>
      <p class="person-title">Managing Director</p>
      <ul class="contact-list">
        <li>
          <svg viewBox="0 0 24 24" fill="none" stroke="currentColor" stroke-width="2.2"><path d="M5 3h4l2 5-2.5 1.5a11 11 0 0 0 6 6L16 13l5 2v4a2 2 0 0 1-2 2A16 16 0 0 1 3 5a2 2 0 0 1 2-2z"/></svg>
          407-555 018 273
        </li>
        <li>
          <svg viewBox="0 0 24 24" fill="currentColor"><path d="M2 5h20v14H2z"/><path d="M2 5l10 8 10-8" fill="none" stroke="#0a0a0a" stroke-width="1.8"/></svg>
          info@brookvane.com
        </li>
        <li>
          <svg viewBox="0 0 24 24" fill="none" stroke="currentColor" stroke-width="1.8"><circle cx="12" cy="12" r="9.5"/><path d="M2.5 12h19M12 2.5c3 3 3 16 0 19M12 2.5c-3 3-3 16 0 19"/></svg>
          www.brookvanedrafting.com
        </li>
      </ul>
      <p class="address">218 Palmetto Row,<br>Orlando FL 32801</p>
    </div>
  </section>

  <section class="card card--back" aria-label="Business card back">
    <p class="brand-name">Brookvane<br>Drafting</p>
  </section>
</main>
</body>
</html>
```